Web design project for exciting Australian start-up

Background
We are looking for a creative and talented web design artist to work alongside our market leading web developer.
• You will be required to create a modern and clean design theme for our website, incorporating selected rustic colour scheme elements for our exciting Australian start-up to operate within the coffee industry.
reoccurring work to be expected to flow to the successful designer.
Requirements
• c. 5 - 10 page website
• Landing page
• Log in/ out
• 404 template
• Typography is emphasised
• Please use either a) typemarrow.com, b) free web fonts, c) brindle fonts
• All design elements in vector format
• Preferably with icons for each header title(i.e. about us, how it works etc) but designer have free reign over how the site looks, so might not be applicable
• All pages to be responsive
• Down to eSlab resolution

High level visual design brief attached - additional pages to be worked from base design.

Design inspiration
• We would like to use design elements from the following sources:
http://www.zandrix.com/halcyon/ (Functionality)
Colour scheme refer to logo and complementary style guide

```html
<!DOCTYPE html>
<html lang="en">
<head>
<meta charset="utf-8">
<title>Roastline – Online Coffee Marketplace</title>
<link rel="stylesheet" href="https://fonts.googleapis.com/css2?family=Arimo:wght@400;700&family=Questrial&display=swap">
<style>
  :root {
    --orange: #f7a534;
    --orange-button: #f28c1a;
    --charcoal: #262626;
    --red: #e6373f;
    --header-wash: rgba(255, 255, 255, 0.82);
    --headline-bg: rgba(20, 14, 10, 0.82);
    --footer-wood: #34271f;
    --footer-panel: rgba(120, 110, 104, 0.55);
    --footer-heading: #ffffff;
    --footer-text: #f2ede8;
    --brand-ink: #222222;
  }
  * { box-sizing: border-box; margin: 0; padding: 0; }
  html, body { width: 1200px; height: 831px; overflow: hidden; }
  body { position: relative; font-family: "Arimo", Arial, sans-serif; background: var(--footer-wood); }

  .hero-photo {
    position: absolute; left: 0; top: 0; width: 1200px; height: 605px;
    background:
      radial-gradient(ellipse 260px 240px at 880px 300px, #e9e6e2 0%, #cfc8c0 55%, rgba(120,80,50,0) 100%),
      radial-gradient(ellipse 500px 300px at 300px 200px, #5a3620 0%, rgba(60,35,20,0) 100%),
      linear-gradient(180deg, #4a2e1c 0%, #3b2416 45%, #5a3a26 75%, #3e2a1e 100%);
  }

  .site-header {
    position: absolute; left: 0; top: 0; width: 1200px; height: 122px;
    background: var(--header-wash);
    border-bottom: 1px solid rgba(255,255,255,0.6);
  }
  .brand {
    position: absolute; display: flex; align-items: center; gap: 10px;
    font-family: "Arimo", Arial, sans-serif; font-weight: 700; color: var(--brand-ink);
  }
  .brand-mark { border-radius: 50%; background: var(--brand-ink); flex: none; }
  .site-header .brand { left: 74px; top: 32px; font-size: 34px; letter-spacing: 2px; }
  .site-header .brand-mark { width: 56px; height: 56px; }

  .account-actions { position: absolute; top: 46px; left: 946px; display: flex; gap: 7px; }
  .account-actions a {
    display: block; height: 30px; line-height: 30px; padding: 0 15px;
    font-size: 12px; font-weight: 700; color: #fff; text-decoration: none; border-radius: 2px;
  }
  .btn-login { background: var(--orange-button); }
  .btn-signup { background: var(--charcoal); }

  .hero-copy { position: absolute; left: 74px; top: 275px; }
  .hero-title { font-size: 37px; font-weight: 700; color: var(--orange); line-height: 1; }
  .hero-title span {
    display: inline-block; background: var(--headline-bg);
    padding: 6px 14px 7px 13px; margin-bottom: 6px;
  }
  .btn-video {
    display: inline-flex; align-items: center; gap: 11px; margin-top: 22px;
    height: 43px; padding: 0 16px 0 15px; background: var(--red); color: #fff;
    font-size: 16px; font-weight: 700; text-decoration: none; letter-spacing: .3px;
  }

  .footer-wood {
    position: absolute; left: 0; top: 605px; width: 1200px; height: 226px;
    background: linear-gradient(90deg, #2f231c 0%, #3d2e25 30%, #33261f 60%, #3f3028 100%);
  }
  .site-footer {
    position: absolute; left: 74px; top: 625px; width: 1052px; height: 190px;
    background: var(--footer-panel); border-radius: 3px;
    font-family: "Questrial", Arial, sans-serif;
  }
  .footer-column { position: absolute; top: 24px; }
  .footer-column h3 {
    font-family: "Arimo", Arial, sans-serif; font-size: 11.5px; font-weight: 700;
    color: var(--footer-heading); margin-bottom: 12px;
  }
  .footer-column ul { list-style: none; }
  .footer-column li { font-size: 11.5px; line-height: 26px; }
  .footer-column a { color: var(--orange); text-decoration: none; }
  .col-help { left: 28px; }
  .col-who { left: 199px; }
  .col-join { left: 363px; }
  .social-list li { display: flex; align-items: center; gap: 13px; }
  .social-square { width: 14px; height: 14px; background: #8a8580; border-radius: 2px; flex: none; }

  .site-footer .brand { right: 30px; top: 30px; font-size: 20px; color: #f4f1ee; gap: 8px; letter-spacing: 1px; }
  .site-footer .brand-mark { width: 36px; height: 36px; background: #f4f1ee; }
  .copyright {
    position: absolute; right: 30px; top: 106px; text-align: right;
    font-size: 11.5px; line-height: 17px; color: var(--footer-text);
  }
  .copyright a { color: var(--orange); text-decoration: none; }
</style>
</head>
<body>
  <div class="hero-photo" role="img" aria-label="Photo of a white cup of coffee on a saucer with cinnamon sticks and star anise, roasted coffee beans spilling from a burlap sack on a wooden table"></div>

  <header class="site-header">
    <div class="brand"><span class="brand-mark"></span>ROASTLINE</div>
    <nav class="account-actions">
      <a class="btn-login" href="#">LOG IN</a>
      <a class="btn-signup" href="#">SIGN UP</a>
    </nav>
  </header>

  <section class="hero-copy">
    <h1 class="hero-title"><span>Australia’s first Online</span><br><span>Coffee Marketplace</span></h1>
    <a class="btn-video" href="#">
      <svg width="26" height="26" viewBox="0 0 26 26" aria-hidden="true">
        <circle cx="13" cy="13" r="11.5" fill="none" stroke="#fff" stroke-width="2"/>
        <path d="M10 7.5 L16.5 13 L10 18.5" fill="none" stroke="#fff" stroke-width="2.4" stroke-linejoin="round"/>
      </svg>
      WATCH VIDEO
    </a>
  </section>

  <div class="footer-wood" role="img" aria-label="Dark brown wooden plank texture"></div>

  <footer class="site-footer">
    <div class="footer-column col-help">
      <h3>HELPFUL INFO</h3>
      <ul>
        <li><a href="#">About us</a></li>
        <li><a href="#">Media enquiries</a></li>
        <li><a href="#">Terms &amp; conditions</a></li>
        <li><a href="#">Privacy policy</a></li>
      </ul>
    </div>
    <div class="footer-column col-who">
      <h3>WHO WE ARE</h3>
      <ul>
        <li><a href="#">How it works</a></li>
        <li><a href="#">FAQ</a></li>
        <li><a href="#">Contact us</a></li>
      </ul>
    </div>
    <div class="footer-column col-join">
      <h3>JOIN US</h3>
      <ul class="social-list">
        <li><span class="social-square"></span><a href="#">Pagepal</a></li>
        <li><span class="social-square"></span><a href="#">Chirpline</a></li>
        <li><span class="social-square"></span><a href="#">Workmesh</a></li>
        <li><span class="social-square"></span><a href="#">Clipstream</a></li>
      </ul>
    </div>

    <div class="brand"><span class="brand-mark"></span>ROASTLINE</div>
    <p class="copyright">Copyright © 2014 <a href="#">Roastline</a><br>All Right Reserved</p>
  </footer>
</body>
</html>
```